Business Card Design Project

Looking for a simple and stylish business card. We are an Advertising Company. The card Must feature the company logo (attached) and also this info.
p: 0481552306
e: sales@rt-media.com.au
w: www.rt-media.com.au
We Advertise mainly using TV screens featured in restaurants and cafe. See website for more about the business.
Not really looking for a plain background, but at the same time do not want to much happening in the Background. I am not really to fussy though with the design or the colour scheme, and I am leaving the creativity part up to you creative designers.

```html
<!DOCTYPE html>
<html lang="en">
<head>
<meta charset="utf-8">
<title>RT Media – Business Card</title>
<link rel="stylesheet" href="https://fonts.googleapis.com/css2?family=Exo+2:ital,wght@0,300;0,400;1,400&display=swap">
<style>
  :root {
    --brand-pink: #e31e5c;
    --brand-blue: #174c9a;
    --card-white: #ffffff;
    --backdrop-light: #f3efe8;
    --backdrop-dark: #d6d0c7;
  }
  html, body {
    margin: 0;
    width: 1200px;
    height: 900px;
    overflow: hidden;
  }
  body {
    background: radial-gradient(ellipse at center, var(--backdrop-light) 0%, var(--backdrop-light) 35%, var(--backdrop-dark) 100%);
    font-family: "Exo 2", sans-serif;
    position: relative;
  }
  .business-card {
    position: absolute;
    left: 255px;
    top: 253px;
    width: 690px;
    height: 394px;
    background: var(--card-white);
    overflow: hidden;
  }
  .top-band {
    position: absolute;
    left: 0;
    top: 0;
    width: 690px;
    height: 254px;
    background: var(--brand-pink);
  }
  .side-stripes {
    position: absolute;
    left: 0;
    top: 0;
    width: 690px;
    height: 394px;
  }
  .holder {
    position: absolute;
    left: 44px;
    top: 22px;
    color: var(--card-white);
    font-style: italic;
    font-weight: 400;
    font-size: 30px;
    line-height: 42px;
  }
  .holder-name {
    display: block;
    padding-left: 22px;
  }
  .contact-list {
    position: absolute;
    right: 20px;
    top: 120px;
    margin: 0;
    padding: 0;
    list-style: none;
    text-align: right;
    color: var(--card-white);
    font-weight: 400;
    font-size: 28px;
    line-height: 39.5px;
  }
  .company-name {
    position: absolute;
    right: 20px;
    top: 262px;
    margin: 0;
    color: var(--brand-blue);
    font-weight: 300;
    font-size: 92px;
    line-height: 120px;
    letter-spacing: 2px;
    white-space: nowrap;
  }
</style>
</head>
<body>
  <div class="business-card">
    <div class="top-band"></div>
    <svg class="side-stripes" viewBox="0 0 690 394" aria-hidden="true">
      <polygon points="0,0 8,0 147,394 0,394" fill="var(--brand-blue)"/>
      <polygon points="0,59 78,394 60,394 0,127" fill="var(--card-white)"/>
    </svg>
    <p class="holder">
      <span class="holder-role">Managing Director</span>
      <span class="holder-name">Mark Talanoa</span>
    </p>
    <ul class="contact-list">
      <li>0481552306</li>
      <li>sales@rt-media.com.au</li>
      <li>www.rt-media.com.au</li>
    </ul>
    <p class="company-name">RT MEDIA</p>
  </div>
</body>
</html>
```